Business Card Design

WE are looking for a premium quality Business Cards for a Law Firm . Copies of our current business card is attached.

Contact Information for Business Card

xyz

```html
<!DOCTYPE html>
<html lang="en">
<head>
<meta charset="utf-8">
<title>Ashcombe Lawyers – Business Card</title>
<link rel="stylesheet" href="https://fonts.googleapis.com/css2?family=Tinos:wght@400;700&display=swap">
<style>
  :root {
    --forest: #0d2a1c;
    --forest-soft: #163a28;
    --gold: #c9a862;
    --white: #ffffff;
    --ink: #111111;
    --backdrop: #2b2e33;
  }
  * { margin: 0; padding: 0; box-sizing: border-box; }
  html, body { width: 1200px; height: 780px; overflow: hidden; }
  body {
    background: var(--backdrop);
    font-family: "Tinos", "Times New Roman", serif;
    display: flex;
    align-items: center;
    justify-content: center;
    gap: 40px;
  }
  .card {
    position: relative;
    width: 560px;
    height: 320px;
    border-radius: 16px;
    overflow: hidden;
  }

  /* Front */
  .card-front { background: var(--white); color: var(--ink); }
  .front-art { position: absolute; inset: 0; }
  .brand-small {
    position: absolute; left: 30px; top: 22px;
    display: flex; align-items: center; gap: 8px;
  }
  .brand-dot {
    width: 22px; height: 22px; border-radius: 50%;
    border: 2px solid var(--gold);
  }
  .brand-small .brand-name {
    font-weight: 700; font-size: 17px; color: var(--forest); letter-spacing: 1px;
  }
  .address {
    position: absolute; left: 30px; top: 60px;
    font-weight: 700; font-size: 13px; line-height: 17px;
  }
  .contacts {
    position: absolute; left: 30px; top: 118px;
    list-style: none; font-weight: 700; font-size: 12.5px; line-height: 17px;
  }
  .contacts li { display: flex; align-items: center; gap: 7px; }
  .contacts svg { width: 11px; height: 11px; flex: none; }
  .person {
    position: absolute; right: 24px; top: 84px; text-align: right;
  }
  .person-name {
    font-weight: 700; font-size: 32px; color: var(--gold); letter-spacing: 1.5px; line-height: 36px;
  }
  .person-role, .person-degree {
    font-weight: 700; font-size: 15px; line-height: 21px;
  }
  .edge-bar {
    position: absolute; right: 0; top: 88px; width: 12px; height: 72px; background: var(--gold);
  }
  .seal {
    position: absolute; left: 330px; top: 186px; width: 124px; height: 124px;
    border-radius: 50%; background: var(--white); border: 7px solid var(--gold);
    display: flex; align-items: center; justify-content: center;
  }
  .seal .brand-name {
    font-weight: 700; font-size: 16px; color: var(--forest); letter-spacing: 1px;
  }

  /* Back */
  .card-back { background: var(--forest); color: var(--white); }
  .brand-emboss {
    position: absolute; left: 0; right: 0; top: 40px;
    display: flex; align-items: center; justify-content: center; gap: 12px;
  }
  .brand-emboss .brand-dot { width: 34px; height: 34px; border-color: var(--forest-soft); border-width: 3px; }
  .brand-emboss .brand-name {
    font-weight: 700; font-size: 30px; color: var(--forest-soft); letter-spacing: 2px;
  }
  .tagline-band {
    position: absolute; left: 0; right: 0; top: 118px; height: 26px;
    background: var(--gold); color: var(--forest);
    font-weight: 700; font-size: 14px; letter-spacing: 1px;
    display: flex; align-items: center; justify-content: center;
  }
  .offices {
    position: absolute; left: 18px; right: 18px; top: 166px;
    display: grid; grid-template-columns: 1fr 1fr 1fr;
  }
  .office { padding: 0 12px; font-weight: 700; font-size: 11.5px; line-height: 16px; }
  .office + .office { border-left: 1px solid rgba(255,255,255,.75); }
  .office-city { color: var(--gold); font-size: 14px; margin-bottom: 4px; letter-spacing: .5px; }
  .office-phone { display: flex; align-items: center; gap: 5px; }
  .office-phone svg { width: 10px; height: 10px; }
</style>
</head>
<body>

<article class="card card-front">
  <svg class="front-art" viewBox="0 0 560 320" aria-hidden="true">
    <path d="M0,208 C18,266 115,292 255,286 C300,284 335,268 370,250 L478,250 L478,320 L0,320 Z" fill="var(--forest)"/>
    <path d="M4,192 C20,256 105,284 220,290" fill="none" stroke="var(--gold)" stroke-width="5"/>
  </svg>

  <div class="brand-small">
    <span class="brand-dot"></span>
    <span class="brand-name">ASHCOMBE LAWYERS</span>
  </div>

  <p class="address">Suite 118, Harbour Chambers,<br>212 Keel Street,<br>Northport VIC 3999</p>

  <ul class="contacts">
    <li><svg viewBox="0 0 12 12"><path d="M3 1 L5 4 L4 5 Q5 7 7 8 L8 7 L11 9 L10 11 Q4 11 1 3 Z" fill="var(--gold)"/></svg>+61 7 5550 0142</li>
    <li><svg viewBox="0 0 12 12"><rect x="3" y="1" width="6" height="10" rx="1" fill="none" stroke="var(--gold)" stroke-width="1.3"/></svg>+61 0400 555 018</li>
    <li><svg viewBox="0 0 12 12"><circle cx="6" cy="6" r="5" fill="none" stroke="var(--gold)" stroke-width="1.3"/><path d="M1 6 H11 M6 1 V11" stroke="var(--gold)" stroke-width="1"/></svg>www.ashcombelawyers.example</li>
    <li><svg viewBox="0 0 12 12"><rect x="1" y="3" width="10" height="7" fill="none" stroke="var(--gold)" stroke-width="1.3"/><path d="M1 3 L6 7 L11 3" fill="none" stroke="var(--gold)" stroke-width="1.1"/></svg>marcus@ashcombelawyers.example</li>
  </ul>

  <div class="person">
    <h1 class="person-name">MARCUS HALE</h1>
    <p class="person-role">Director and Principal Solicitor</p>
    <p class="person-degree">MBA, Juris Doctor</p>
  </div>
  <span class="edge-bar"></span>

  <div class="seal"><span class="brand-name">ASHCOMBE</span></div>
</article>

<article class="card card-back">
  <div class="brand-emboss">
    <span class="brand-dot"></span>
    <span class="brand-name">ASHCOMBE LAWYERS</span>
  </div>

  <p class="tagline-band">CLEAR COUNSEL. STRONG OUTCOMES. EVERY TIME</p>

  <div class="offices">
    <section class="office">
      <h2 class="office-city">NORTHPORT</h2>
      <p>Level 12, 40 Elder Street,<br>NORTHPORT, VIC 3999</p>
      <p class="office-phone"><svg viewBox="0 0 12 12"><path d="M3 1 L5 4 L4 5 Q5 7 7 8 L8 7 L11 9 L10 11 Q4 11 1 3 Z" fill="var(--gold)"/></svg>+61 03 5550 0173</p>
    </section>
    <section class="office">
      <h2 class="office-city">EASTVALE</h2>
      <p>Level 9, Meridian House<br>18 Quarry Road<br>EASTVALE, NSW 2999</p>
      <p class="office-phone"><svg viewBox="0 0 12 12"><path d="M3 1 L5 4 L4 5 Q5 7 7 8 L8 7 L11 9 L10 11 Q4 11 1 3 Z" fill="var(--gold)"/></svg>+61 02 5550 0196</p>
    </section>
    <section class="office">
      <h2 class="office-city">WESTBAY</h2>
      <p>Level 21, Tern Tower<br>75 Marlow Terrace<br>WESTBAY, WA 6999</p>
      <p class="office-phone"><svg viewBox="0 0 12 12"><path d="M3 1 L5 4 L4 5 Q5 7 7 8 L8 7 L11 9 L10 11 Q4 11 1 3 Z" fill="var(--gold)"/></svg>+61 08 5550 0127</p>
    </section>
  </div>
</article>

</body>
</html>
```